The logo name is "Harbor Skin". The name of the product will be "Cutaneous Comfort". This product is specifically formulated for amputees. Therefore under the product name it should state "for amputees". The catch phrase will be "Experience Harbor find Calmness"
These are the things we need on the label:
Logo, product name, "for amputees", "Experience Harbor find Calmness", Safe, Effective, Directions: spray on problem areas, no need to dry off. harborskin.example, Made in Canada, 500ml.
The MOST IMPORTANT and therefore the most prominent thing on this lable will be the LOGO! The second most prominent thing will be the word "Comfort" We want to keep it very plain, very simple, very unclutered. Keep in mind that this lable will be placed on a white bottle or have a white back ground. The 500ml white PE bottle with trigger sprayer will have a tear drop label. See attached die line (S-294).
We want to stay with the colours that goes with the colour scheme of the logo. See attached logo. Soft colours. We do not want a picture! We would like the lable to be classy and rich.
Updates
The logo name is "Harbor Skin". The name of the product will be "Cutaneous Comfort". This product is specificlly formulated for amputees. Therefore under the product name it should state "for amputees". The catch phrase will be "Experience Harbor find Calmness"
Logo, product name, "for amputees", catch phrase "Experience Harbor find Calmness", Clean, Safe, Effective, Directions: spray on problem areas, no need to dry off. Also Harbor Skin Corpation, harborskin.example, Made in Canada, 500ml.
We want to stay with the colour scheme of the logo. See attached logo. Soft colours. We do not want a picture! We would like the lable to be classy and rich.
This is the offical directive that came from the governing panal of this lable. This panal it not know where it wanted to take this lable that would represent this line until they review all of your submissions, thank you for all your talented hard work. But now it is clear it is time to regroup and hit this objective.
Project Deadline Extended
Reason: New restrictions on lable wording for this product.
Target Market(s)
Amputees and Parents of.
Industry/Entity Type
Product
Requirements
Must have
- Final product to be in a pdf or an illustrator file

```html
<!DOCTYPE html>
<html lang="en">
<head>
<meta charset="utf-8">
<title>Harbor Skin – Cutaneous Comfort Label</title>
<link href="https://fonts.googleapis.com/css2?family=Roboto+Condensed:ital,wght@0,400;0,700;1,700&family=Alfa+Slab+One&family=Roboto:wght@400;700&display=swap" rel="stylesheet">
<style>
  :root{
    --bg:#e6e7e8;
    --label-white:#ffffff;
    --mist:#cfe9e6;
    --teal:#2fbcb4;
    --teal-soft:#a9dcd7;
    --band-light:#e4f4f2;
    --green:#0f6a49;
    --green-deep:#0d5a3c;
    --orange:#f7b84d;
    --ink:#1d3d31;
  }
  *{margin:0;padding:0;box-sizing:border-box}
  html,body{width:1200px;height:1000px;overflow:hidden;background:var(--bg)}
  .canvas{position:relative;width:1200px;height:1000px}
  .label-shape{position:absolute;left:0;top:0}
  .label-content{position:absolute;left:330px;top:0;width:540px;height:1000px;text-align:center}
  .brand{position:absolute;top:400px;left:0;width:100%;display:flex;justify-content:center;align-items:center;gap:12px}
  .brand-mark{width:38px;height:38px;background:var(--teal)}
  .brand-name{font-family:"Roboto Condensed",sans-serif;font-weight:700;font-size:44px;color:var(--green);letter-spacing:.5px}
  .product-line{position:absolute;top:492px;left:0;width:100%;font-family:"Roboto",sans-serif;font-size:26px;letter-spacing:7px;color:#fff;line-height:1.1}
  .product-name{position:absolute;top:524px;left:0;width:100%;font-family:"Alfa Slab One",serif;font-size:60px;letter-spacing:4px;color:var(--orange);-webkit-text-stroke:1.5px #fff;line-height:1}
  .lower{position:absolute;top:628px;left:0;width:100%;display:flex;flex-direction:column;align-items:center}
  .audience{width:170px;height:64px;background:var(--teal);color:#fff;border-bottom:5px solid var(--teal-soft)}
  .audience-for{display:block;font-family:"Roboto",sans-serif;font-size:17px;padding-top:5px;line-height:1}
  .audience-main{display:block;font-family:"Roboto Condensed",sans-serif;font-style:italic;font-weight:700;font-size:30px;line-height:1.1}
  .tagline{margin-top:18px;font-family:"Roboto Condensed",sans-serif;font-weight:700;font-size:23px;line-height:1.2;color:var(--orange)}
  .claims{margin-top:8px;width:220px;height:22px;background:var(--green-deep);color:#fff;font-family:"Roboto Condensed",sans-serif;font-style:italic;font-weight:700;font-size:13px;letter-spacing:1.2px;line-height:22px}
  .fine-print{margin-top:18px;font-family:"Roboto Condensed",sans-serif;font-size:11px;color:var(--ink);line-height:1.3}
  .fine-print strong{font-weight:700}
  .fine-print p+p{margin-top:6px}
  .web{margin-top:10px;font-family:"Roboto",sans-serif;font-weight:700;font-size:11px;line-height:1.3;letter-spacing:3px;color:var(--ink)}
  .origin{margin-top:14px;font-family:"Roboto Condensed",sans-serif;font-size:11px;line-height:1.3;color:var(--ink)}
</style>
</head>
<body>
<div class="canvas">
  <svg class="label-shape" width="1200" height="1000" viewBox="0 0 1200 1000">
    <defs>
      <linearGradient id="labelFill" x1="0" y1="0" x2="0" y2="1">
        <stop offset="0" stop-color="var(--mist)"/>
        <stop offset="0.35" stop-color="var(--label-white)"/>
        <stop offset="0.7" stop-color="var(--label-white)"/>
        <stop offset="1" stop-color="var(--mist)"/>
      </linearGradient>
      <linearGradient id="bandFill" x1="0" y1="0" x2="0" y2="1">
        <stop offset="0" stop-color="var(--band-light)"/>
        <stop offset="0.12" stop-color="var(--teal-soft)"/>
        <stop offset="0.88" stop-color="var(--teal-soft)"/>
        <stop offset="1" stop-color="var(--band-light)"/>
      </linearGradient>
      <clipPath id="labelClip">
        <path d="M830 100 C860 300 870 500 870 700 C870 850 780 925 600 925 C420 925 330 850 330 700 C330 450 640 250 830 100 Z"/>
      </clipPath>
    </defs>
    <path d="M830 100 C860 300 870 500 870 700 C870 850 780 925 600 925 C420 925 330 850 330 700 C330 450 640 250 830 100 Z" fill="url(#labelFill)"/>
    <rect x="300" y="484" width="600" height="106" fill="url(#bandFill)" clip-path="url(#labelClip)"/>
  </svg>

  <div class="label-content">
    <div class="brand">
      <span class="brand-mark"></span>
      <span class="brand-name">Harbor Skin</span>
    </div>
    <div class="product-line">Cutaneous</div>
    <div class="product-name">COMFORT</div>
    <div class="lower">
      <div class="audience">
        <span class="audience-for">For</span>
        <span class="audience-main">AMPUTEES</span>
      </div>
      <div class="tagline">Experience Harbor Find Calmness</div>
      <div class="claims">CLEAN, SAFE &amp; EFFECTIVE</div>
      <div class="fine-print">
        <p><strong>Directions:</strong><br><strong>Spray on problem areas, no need to dry off.</strong></p>
        <p><strong>Manufactured by:</strong><br>Harbor Skin Corporations</p>
      </div>
      <div class="web">www.harborskin.example</div>
      <div class="origin">Made in Canada &nbsp;|&nbsp; 500mL</div>
    </div>
  </div>
</div>
</body>
</html>
```